CrestHornSupply.com

I need a new webdesign for a company in the Crest Horn/SF Bay area that showcases the financial benefits of buying used band instruments for junior high students.This would be opposed to the current and costly option of renting cheap quality instruments from the 2 or 3 local music stores that charge a monthly fee that over the years charges the buyer 3 or 4x over..
Instruments: focus in on Alto Sax, Trumpet, Flute, Clarinet, Trombone, Tenor Sax, Baritone
Target middle schools are Larkfield Middle School and Maple Middle School in Crest Horn, CA. Both have award winning band programs.
Files attached may or may not be important.
Tabs Needed and funtional
Contact
Shopping Cart
Select Instrument
Checkout
Add to Cart, etc.
Instuments
quantity, etc.
trade in your instrument/sell your instrument
ability to add or take away new instruments for sale. including pictures
Additional questions or info, feel free to ask
Updates
Hi Designers,
Project Deadline Extended
Reason: In the next week you will be receiving specific content that will be required to be had on the website.
New desigins are still welcome. Please continue to contact me if you have questions about your individual designs.
Thanks!
Crest Horn

```html
<!DOCTYPE html>
<html lang="en">
<head>
<meta charset="utf-8">
<title>Crest Horn – Band Instruments</title>
<link href="https://fonts.googleapis.com/css2?family=Jost:wght@300;400;500&family=Open+Sans:wght@400;600&display=swap" rel="stylesheet">
<style>
:root{
  --green:#7cad2a;
  --green-dark:#5f8c1a;
  --orange:#f07a12;
  --ink:#2b2b2b;
  --muted:#5a5a5a;
  --footer:#1b1b1b;
  --footer-line:#2e2e2e;
  --white:#ffffff;
}
*{box-sizing:border-box;margin:0;padding:0}
html,body{width:679px;height:1200px;overflow:hidden;background:var(--white)}
body{position:relative;font-family:"Open Sans",Arial,sans-serif;color:var(--ink)}
.abs{position:absolute}
.head{font-family:"Jost",Arial,sans-serif}

/* header */
.site-header{left:0;top:0;width:679px;height:57px;background:linear-gradient(#fff,#eceded)}
.brand{left:63px;top:14px;font-family:"Jost",sans-serif;font-size:21px;font-weight:400;color:var(--ink);letter-spacing:.5px;display:flex;align-items:center;gap:6px}
.brand .mark{width:9px;height:9px;background:var(--orange);border-radius:50%}
.top-links{right:63px;top:7px;font-size:6.5px;color:#555;display:flex;gap:10px}
.search{left:422px;top:26px;width:122px;height:17px;border:1px solid #ccc;border-radius:9px;background:#fff;font-size:6.5px;color:#888;padding:4px 9px}
.search svg{position:absolute;right:7px;top:4px}
.cart{left:548px;top:26px;width:68px;height:17px;border:1px solid #ccc;border-radius:9px;background:#fff;font-size:6.5px;color:#777;padding:4px 0 0 22px}
.cart b{color:var(--orange);margin-left:5px}

/* nav */
.main-nav{left:0;top:57px;width:679px;height:26px;background:var(--green);display:flex;padding-left:63px}
.main-nav a{font-size:7.5px;color:#fff;text-decoration:none;line-height:26px;padding:0 12.5px;border-right:1px solid rgba(0,0,0,.12);font-weight:600}
.main-nav a.active{background:var(--orange);padding:0 17px}

/* hero */
.hero{left:0;top:83px;width:679px;height:299px;background:linear-gradient(100deg,#1c2a24 0%,#2f4a3e 45%,#425a52 70%,#252f2c 100%)}
.hero-text{left:63px;top:157px;color:#fff}
.hero-text .welcome{font-family:"Jost",sans-serif;font-weight:300;font-size:18px;letter-spacing:.5px}
.hero-text .name{font-family:"Jost",sans-serif;font-size:36px;font-weight:400;line-height:40px;margin-top:1px}
.hero-text p{font-size:10px;line-height:14.5px;width:240px;margin-top:4px}
.btn-shop{left:64px;top:279px;width:111px;height:26px;border-radius:13px;background:linear-gradient(#8cc43a,#6a9c1f);color:#fff;font-family:"Jost",sans-serif;font-size:11px;display:flex;align-items:center;justify-content:center;gap:6px}
.slide-arrow{top:217px;width:26px;height:26px;border-radius:50%;background:rgba(0,0,0,.35);display:flex;align-items:center;justify-content:center}

/* sections */
.section-title{left:0;width:679px;text-align:center;font-family:"Jost",sans-serif;font-size:28px;font-weight:400;color:var(--ink);display:flex;justify-content:center;align-items:center;gap:10px}
.section-title .rule{width:70px;height:1px;background:#bbb}
.section-title em{font-style:normal;color:var(--green)}
.section-copy{left:66px;width:547px;text-align:center;font-size:10px;line-height:14px;color:var(--muted)}
.section-copy.small{left:90px;width:540px;font-size:8.5px;line-height:13px;color:#777}
.btn-more{left:294px;top:507px;width:91px;height:24px;border-radius:12px;background:var(--orange);color:#fff;font-family:"Jost",sans-serif;font-size:9.5px;display:flex;align-items:center;justify-content:center;gap:4px}

/* instrument tiles */
.tile{color:#fff;overflow:hidden}
.tile h3{font-family:"Jost",sans-serif;font-weight:400;font-size:15.5px;line-height:16px;position:absolute;top:13px}
.tile p{font-size:7px;line-height:8.5px;position:absolute;top:32px;width:92px}
.tile .mini-btn{position:absolute;top:57px;width:59px;height:16px;border:1px solid #fff;font-size:5.5px;font-weight:600;display:flex;align-items:center;justify-content:center;gap:3px}
.tile.left h3,.tile.left p,.tile.left .mini-btn{left:13px}
.tile.right h3,.tile.right p{right:14px;text-align:right}
.tile.right .mini-btn{right:14px}
.tile.center{text-align:center}
.tile.center h3{left:0;width:100%;top:114px}
.tile.center p{left:10px;width:161px;top:135px;font-size:8px;line-height:10.5px}
.tile.center .mini-btn{left:54px;top:180px;width:75px;height:20px;font-size:7.5px}

/* partners */
.partners{left:0;top:980px;width:679px;height:31px;border-top:1px solid #ddd;border-bottom:1px solid #ddd;display:flex;padding-left:70px}
.partner{width:69px;height:31px;border-left:1px solid #e3e3e3;display:flex;align-items:center;justify-content:center}
.partner:last-child{border-right:1px solid #e3e3e3}
.partner span{width:34px;height:10px;border-radius:5px;background:#9a9a9a}

/* footer */
.site-footer{left:0;top:1011px;width:679px;height:189px;background:var(--footer)}
.foot-title{font-family:"Jost",sans-serif;font-size:12px;color:var(--green)}
.sitemap{left:63px;top:1036px}
.sitemap ul{list-style:none;margin-top:9px}
.sitemap li{font-size:7.5px;color:#9a9a9a;line-height:14.5px}
.sitemap li.current{color:#fff}
.newsletter{left:159px;top:1036px;width:130px}
.newsletter p{font-size:6px;line-height:8.5px;color:#aaa;margin-top:9px}
.field{width:126px;height:18px;background:#fff;border:1px solid #ccc;border-radius:2px;font-size:6px;color:#888;padding:5px 8px;margin-top:6px}
.subscribe{width:58px;height:19px;background:var(--orange);color:#fff;font-size:7px;display:flex;align-items:center;justify-content:center;margin-top:6px;border-radius:2px}
.follow{left:346px;top:1036px}
.follow ul{list-style:none;margin-top:7px}
.follow li{display:flex;align-items:center;gap:9px;font-size:7.5px;color:#9a9a9a;height:19px}
.follow li i{width:15px;height:15px;border:1px solid #666;border-radius:50%;display:block}
.foot-brand{left:490px;top:1063px;font-family:"Jost",sans-serif;font-size:20px;color:#8a8a8a;display:flex;align-items:center;gap:5px}
.foot-brand .mark{width:8px;height:8px;border-radius:50%;background:#8a8a8a}
.payment{left:491px;top:1097px}
.cards{display:flex;gap:5px;margin-top:7px}
.cards span{width:22px;height:13px;border-radius:2px;background:#d8d8d8}
.foot-rule{left:0;top:1170px;width:679px;height:1px;background:var(--footer-line)}
.copyright{left:0;top:1177px;width:679px;text-align:center;font-size:7.5px;color:#aaa}
</style>
</head>
<body>

<header class="site-header abs">
  <div class="brand abs">CREST <span class="mark"></span> HORN</div>
  <div class="top-links abs"><span>My Wishlist</span><span>|</span><span>My Account</span><span>|</span><span>Log in</span></div>
  <div class="search abs">Search
    <svg width="8" height="8" viewBox="0 0 10 10"><circle cx="4" cy="4" r="3" fill="none" stroke="#f07a12" stroke-width="1.5"/><line x1="6.2" y1="6.2" x2="9" y2="9" stroke="#f07a12" stroke-width="1.5"/></svg>
  </div>
  <div class="cart abs">
    <svg class="abs" style="left:9px;top:4px" width="10" height="8" viewBox="0 0 10 8"><path d="M0 1h2l1 4h6l1-3H2.5" fill="none" stroke="#777" stroke-width="1"/><circle cx="4" cy="7" r=".8" fill="#777"/><circle cx="8" cy="7" r=".8" fill="#777"/></svg>
    CART <b>0</b> &#9662;
  </div>
</header>

<nav class="main-nav abs">
  <a class="active">HOME</a><a>INSTRUMENT</a><a>CHECKOUT</a><a>QUANTITY</a><a>SHOPPING CART</a><a>CONTACT US</a><a>MY ACCOUNT</a>
</nav>

<section class="hero abs" role="img" aria-label="Photo of a marching band member in green uniform holding a brass instrument"></section>
<div class="slide-arrow abs" style="left:8px"><svg width="7" height="10"><path d="M5 1 1 5l4 4" fill="none" stroke="#ddd" stroke-width="1.3"/></svg></div>
<div class="slide-arrow abs" style="left:645px"><svg width="7" height="10"><path d="M2 1l4 4-4 4" fill="none" stroke="#ddd" stroke-width="1.3"/></svg></div>
<div class="hero-text abs">
  <div class="welcome">WELCOME TO</div>
  <div class="name">CREST HORN</div>
  <p>Lorem Ipsum is simply dummy text of typesetting industry. Lorem Ipsum has been the industry's standard dummy text ever since</p>
</div>
<div class="btn-shop abs">
  <svg width="11" height="9" viewBox="0 0 11 9"><path d="M1 3h9l-1 5H2z" fill="#fff"/><path d="M3 3l2.5-2.5L8 3" fill="none" stroke="#fff"/></svg>SHOP NOW
</div>

<h2 class="section-title abs" style="top:412px"><span class="rule"></span>ABOUT <em>US</em><span class="rule"></span></h2>
<p class="section-copy abs" style="top:450px">Lorem Ipsum is simply dummy text of typesetting industry. Lorem Ipsum has been. the industry's standard dummy text ever since the 1500s, when an unknown printer took a galley of type and scrambled it to make a type specimen book.  It has survived not only five centuries, but also the leap into electronic.</p>
<div class="btn-more abs">VIEW MORE <svg width="8" height="8"><circle cx="4" cy="4" r="3.3" fill="none" stroke="#fff" stroke-width=".8"/><path d="M3.3 2.5 4.8 4 3.3 5.5" fill="none" stroke="#fff" stroke-width=".8"/></svg></div>

<h2 class="section-title abs" style="top:560px"><span class="rule"></span>OUR <em>INSTRUMENT</em><span class="rule"></span></h2>
<p class="section-copy small abs" style="top:599px">Lorem Ipsum is simply dummy text of typesetting industry. Lorem Ipsum has been. the industry's standard dummy text ever since the 1500s, when an unknown printer took a galley of type and scrambled it to make a type specimen book.  It has survived not only five centuries, but also the leap into electronic typesetting.</p>

<article class="tile left abs" style="left:64px;top:659px;width:174px;height:89px;background:linear-gradient(90deg,#3a3a44,#8a8a96 60%,#c8c6d0)" role="img" aria-label="Photo of an alto saxophone in its case">
  <h3>ALTO SAX</h3><p>It is a long established fact that a readerbe.</p><div class="mini-btn">&#8962; SHOP NOW</div>
</article>
<article class="tile left abs" style="left:64px;top:758px;width:174px;height:89px;background:linear-gradient(90deg,#4a4a4c,#8a8478 60%,#a89060)" role="img" aria-label="Photo of a brass trumpet">
  <h3>TRUMPET</h3><p>It is a long established fact that a readerbe.</p><div class="mini-btn">&#8962; SHOP NOW</div>
</article>
<article class="tile left abs" style="left:64px;top:858px;width:174px;height:89px;background:linear-gradient(90deg,#1e2a48,#5a6a90 60%,#cfd6e6)" role="img" aria-label="Photo of a silver flute">
  <h3>FLUTE</h3><p>It is a long established fact that a readerbe.</p><div class="mini-btn">&#8962; SHOP NOW</div>
</article>
<article class="tile center abs" style="left:250px;top:659px;width:180px;height:289px;background:linear-gradient(#3a3836,#2a2826 60%,#403c38)" role="img" aria-label="Photo of a row of black clarinets standing upright">
  <h3>CLARINET</h3><p>It is a long established fact that a reader will be distracted by the readable content of a page when looking.</p><div class="mini-btn">&#8962; SHOP NOW</div>
</article>
<article class="tile right abs" style="left:443px;top:659px;width:174px;height:89px;background:linear-gradient(90deg,#c8c0a8,#8a7a5a 50%,#5a5448)" role="img" aria-label="Photo of a trombone">
  <h3>TROMBONE</h3><p>It is a long established fact that a readerbe.</p><div class="mini-btn">&#8962; SHOP NOW</div>
</article>
<article class="tile right abs" style="left:443px;top:758px;width:174px;height:89px;background:linear-gradient(90deg,#3a3a3a,#6a5a38 50%,#2a2a2a)" role="img" aria-label="Photo of a tenor saxophone in an open case">
  <h3>TENOR SAX</h3><p>It is a long established fact that a readerbe.</p><div class="mini-btn">&#8962; SHOP NOW</div>
</article>
<article class="tile right abs" style="left:443px;top:859px;width:174px;height:89px;background:linear-gradient(90deg,#222a38,#6a7484 50%,#1e2430)" role="img" aria-label="Photo of a silver baritone horn">
  <h3>TENOR SAX</h3><p>It is a long established fact that a readerbe.</p><div class="mini-btn">&#8962; SHOP NOW</div>
</article>

<div class="partners abs">
  <div class="partner"><span></span></div><div class="partner"><span></span></div><div class="partner"><span></span></div><div class="partner"><span></span></div>
  <div class="partner"><span></span></div><div class="partner"><span></span></div><div class="partner"><span></span></div><div class="partner"><span></span></div>
</div>

<footer class="site-footer abs"></footer>
<div class="sitemap abs">
  <div class="foot-title">Site Map</div>
  <ul><li class="current">Home</li><li>About us</li><li>Instrument</li><li>Checkout</li><li>Quantity</li><li>Shopping cart</li><li>Contact Us</li></ul>
</div>
<div class="newsletter abs">
  <div class="foot-title">Signup to Our Newsletters</div>
  <p>Lorem Ipsum is simply dummy text of the printing and typesetting industry.</p>
  <div class="field">Name</div>
  <div class="field">Email</div>
  <div class="subscribe">SUBSCRIBE</div>
</div>
<div class="follow abs">
  <div class="foot-title">Follow Us</div>
  <ul><li><i></i>Chirper</li><li><i></i>FaceSpace</li><li><i></i>Rss</li><li><i></i>LinkUp</li><li><i></i>Orbit+</li></ul>
</div>
<div class="foot-brand abs">CREST <span class="mark"></span> HORN</div>
<div class="payment abs">
  <div class="foot-title">Payment Option</div>
  <div class="cards"><span></span><span></span><span></span><span></span><span></span></div>
</div>
<div class="foot-rule abs"></div>
<div class="copyright abs">© 2014 Crest Horn. All Rights Reserved. Terms &amp; conditions</div>

</body>
</html>
```